Option Sheet

We need a one page option sheet with a left to right reading of the five options. It should be a one sheet, multiple colors and definitive separations between options This is used in a sales consultation. Backround or colors not in option need to have the follow RGB value (5 red, 20 green, 63 blue)

We added a smaller text file, please change that point

Target Market(s)

Divorce

Industry/Entity Type

Legal

Requirements
Must have
• 1) All five options left to right
• 2)language included in sheet

```html
<!DOCTYPE html>
<html lang="en">
<head>
<meta charset="utf-8">
<title>Five Options - Divorce</title>
<link rel="stylesheet" href="https://fonts.googleapis.com/css2?family=Montserrat:wght@400;500;600&family=Oswald:wght@500&family=Open+Sans:wght@400&display=swap">
<style>
  :root {
    --page: #ffffff;
    --title: #1b6f98;
    --rule: #1b6f98;
    --option-bg: #0c2b4c;
    --adv-bg: #1a6f99;
    --adv-head: #1b6f98;
    --dis-head: #124e66;
    --dis-light: #2a6679;
    --dis-dark: #15536b;
    --line: rgba(255,255,255,0.22);
    --text: #ffffff;
  }
  * { box-sizing: border-box; margin: 0; padding: 0; }
  html, body { width: 1200px; height: 849px; overflow: hidden; background: var(--page); }
  .sheet { position: relative; width: 1200px; height: 849px; }

  .sheet-title {
    position: absolute; left: 51px; top: 44px;
    font: 400 46px/1 "Montserrat", sans-serif;
    color: var(--title); letter-spacing: 0.5px; word-spacing: 6px;
  }
  .title-rule {
    position: absolute; left: 51px; top: 112px; width: 1110px; height: 2px; background: var(--rule);
  }

  .column-head {
    position: absolute; top: 142px; height: 36px;
    font: 600 20px/36px "Montserrat", sans-serif; color: var(--text);
  }
  .column-head.advantage { left: 302px; width: 398px; background: var(--adv-head); padding-left: 40px; }
  .column-head.disadvantage { left: 700px; width: 461px; background: var(--dis-head); padding-left: 16px; }

  .options { position: absolute; left: 53px; top: 199px; width: 1108px; }
  .option { display: flex; height: 116px; margin-bottom: 4.5px; }

  .option-name {
    width: 249px; background: var(--option-bg); display: flex; align-items: center; padding-left: 16px;
  }
  .option-number {
    font: 500 58px/1 "Oswald", sans-serif; color: var(--text); width: 50px;
  }
  .option-label {
    font: 500 21px/1.3 "Montserrat", sans-serif; color: var(--text); padding-left: 14px;
  }

  .advantages, .disadvantages { display: flex; flex-direction: column; }
  .advantages { width: 398px; background: var(--adv-bg); }
  .disadvantages { width: 461px; }
  .point {
    flex: 1 1 0; border-bottom: 1px solid var(--line);
    display: flex; align-items: center; color: var(--text);
    font-family: "Open Sans", sans-serif;
  }
  .point:last-child { border-bottom: none; }
  .advantages .point { font-size: 13.5px; padding-left: 16px; }
  .disadvantages .point { font-size: 12px; line-height: 1.3; padding: 0 12px 0 16px; }
  .disadvantages .point:nth-child(odd) { background: var(--dis-light); }
  .disadvantages .point:nth-child(even) { background: var(--dis-dark); }
  .disadvantages .point.tall { flex-grow: 1.6; }
</style>
</head>
<body>
<div class="sheet">
  <h1 class="sheet-title">Five Options - Divorce</h1>
  <div class="title-rule"></div>

  <div class="column-head advantage">Advantage</div>
  <div class="column-head disadvantage">Disadvantage</div>

  <div class="options">
    <section class="option">
      <div class="option-name"><span class="option-number">1</span><span class="option-label">Do Nothing</span></div>
      <div class="advantages">
        <p class="point">Stay married</p>
        <p class="point">No life Changes</p>
        <p class="point"></p>
        <p class="point"></p>
      </div>
      <div class="disadvantages">
        <p class="point">Remain unhappy, depressed, anxious.</p>
        <p class="point">Money and assets may disappear.</p>
        <p class="point">What is going to change?</p>
        <p class="point"></p>
      </div>
    </section>

    <section class="option">
      <div class="option-name"><span class="option-number">2</span><span class="option-label">Go to<br>Counseling</span></div>
      <div class="advantages">
        <p class="point">Reconcile marriage</p>
        <p class="point">Help make a better life</p>
        <p class="point"></p>
        <p class="point"></p>
      </div>
      <div class="disadvantages">
        <p class="point">Past issues are highlighted and may drudge up old wounds.</p>
        <p class="point">It may just clarify the reasons you need to separate and/or divorce.</p>
        <p class="point">Both parties must be invested and willing to participate.</p>
        <p class="point"></p>
      </div>
    </section>

    <section class="option">
      <div class="option-name"><span class="option-number">3</span><span class="option-label">Do it Yourself</span></div>
      <div class="advantages">
        <p class="point">No attorney fees</p>
        <p class="point">You are your on attorney</p>
        <p class="point"></p>
        <p class="point"></p>
      </div>
      <div class="disadvantages">
        <p class="point">People often find that what is “fair,” may in fact, not be truly fair.</p>
        <p class="point">Often times, people do not know the risks.</p>
        <p class="point">Complicated legal system within intrigue rules.</p>
        <p class="point tall">Unsure how to complete the necessary paperwork and meet the deadlines.</p>
      </div>
    </section>

    <section class="option">
      <div class="option-name"><span class="option-number">4</span><span class="option-label">Limited<br>Representation</span></div>
      <div class="advantages">
        <p class="point">Balance between going alone</p>
        <p class="point">and our limited involvement in the case</p>
        <p class="point"></p>
        <p class="point"></p>
      </div>
      <div class="disadvantages">
        <p class="point">Our terms may not benefit from our legal knowledge.</p>
        <p class="point tall">The legal consequences of your legal documents will not be explained to you so that you can formulate a plan for handling the rest of your case.</p>
        <p class="point tall">Your spouse or other parties may cause your legal fees to increase significantly without action on your part.</p>
      </div>
    </section>

    <section class="option">
      <div class="option-name"><span class="option-number">5</span><span class="option-label">Hire Us</span></div>
      <div class="advantages">
        <p class="point">Gain the full benefits of our experience</p>
        <p class="point">Have a team of Family Law focus attorneys</p>
        <p class="point">Often saves you or makes you money in the long run</p>
        <p class="point">Save you time, energy and stress</p>
      </div>
      <div class="disadvantages">
        <p class="point">Initial cost</p>
        <p class="point"></p>
        <p class="point"></p>
        <p class="point"></p>
      </div>
    </section>
  </div>
</div>
</body>
</html>
```